Healthcare and Professional IT Services Company need a redesigned business card

We are a IT Services company that targets small medical practices and professional business such as Attorneys, Accounts, Architects etc. We want to communicate a professional yet friendly image using recent logo redesign here on ArtHarbor. Like to see the colors blue and orange in the design. Must use the Tall Pine Computing as displayed in the new logo - then also want to incorporate the fish logo as well.

Target Market(s)

Small medical and professional services

Industry/Entity Type

It Company

Contact Information for Business Card

The usual stuff, place for name address phone website. Also maybe our tagline which is "rooted in reliable tech"

Requirements
Must have
• My new logo and the fish somewhere on the card

```html
<!DOCTYPE html>
<html lang="en">
<head>
<meta charset="utf-8">
<title>Tall Pine Computing – Business Card</title>
<link rel="stylesheet" href="https://fonts.googleapis.com/css2?family=Open+Sans:wght@400;600;700&display=swap">
<style>
  :root {
    --bg: #2a2b2d;
    --brand-blue: #0a93d8;
    --brand-blue-deep: #0678b9;
    --brand-blue-light: #27a8e6;
    --paper: #ffffff;
    --ink-light: #ffffff;
    --accent-orange: #e9953a;
  }
  * { box-sizing: border-box; margin: 0; padding: 0; }
  html, body {
    width: 1200px; height: 871px; overflow: hidden;
    background: var(--bg);
    font-family: "Open Sans", Arial, sans-serif;
  }
  .stage {
    width: 1200px; height: 871px;
    display: flex; align-items: center; justify-content: center; gap: 40px;
  }
  .card {
    position: relative;
    width: 540px; height: 309px;
    overflow: hidden;
    box-shadow: 0 12px 30px rgba(0,0,0,.45);
  }
  /* Back side */
  .card--back {
    background: linear-gradient(135deg, var(--brand-blue-light) 0%, var(--brand-blue) 55%, var(--brand-blue-deep) 100%);
  }
  .back-name {
    position: absolute; left: 0; right: 0; top: 104px;
    text-align: center;
    color: var(--ink-light);
    font-weight: 600; font-size: 34px; letter-spacing: .5px;
  }
  .tagline {
    position: absolute; left: 0; right: 0; bottom: 30px;
    text-align: center;
    color: var(--ink-light);
    font-weight: 600; font-size: 16px; letter-spacing: .3px;
  }
  /* Front side */
  .card--front { background: var(--paper); }
  .front-shape { position: absolute; inset: 0; }
  .contact {
    position: absolute; left: 34px; top: 40px;
    color: var(--ink-light);
  }
  .contact-name { font-weight: 700; font-size: 19px; line-height: 1.1; }
  .contact-role { font-size: 14px; margin-bottom: 22px; }
  .contact-address { font-size: 13px; line-height: 1.35; margin-bottom: 6px; padding-left: 14px; }
  .contact-list { list-style: none; font-size: 13px; line-height: 1.45; }
  .contact-list li { display: flex; align-items: center; gap: 10px; }
  .contact-list svg { width: 13px; height: 13px; flex: none; }
  .brand {
    position: absolute; right: 40px; top: 0; bottom: 0; width: 220px;
    display: flex; align-items: center; justify-content: center; gap: 10px;
  }
  .brand-dot {
    width: 14px; height: 14px; border-radius: 50%;
    background: var(--accent-orange); flex: none;
  }
  .brand-name {
    color: var(--brand-blue);
    font-weight: 600; font-size: 26px; line-height: 1.1;
  }
</style>
</head>
<body>
<main class="stage">
  <section class="card card--back" aria-label="Business card back">
    <p class="back-name">Tall Pine Computing</p>
    <p class="tagline">rooted in reliable tech</p>
  </section>

  <section class="card card--front" aria-label="Business card front">
    <svg class="front-shape" viewBox="0 0 540 309" preserveAspectRatio="none" aria-hidden="true">
      <path d="M0 0 H360 C280 50 250 170 262 309 H0 Z" fill="var(--brand-blue)"/>
      <path d="M378 0 C300 50 268 150 276 270 C282 160 310 70 392 0 Z" fill="var(--brand-blue)"/>
    </svg>

    <div class="contact">
      <p class="contact-name">Mark Rowan</p>
      <p class="contact-role">President</p>
      <p class="contact-address">2417 Harbor Lane<br>Glenwood, NY 11020</p>
      <ul class="contact-list">
        <li>
          <svg viewBox="0 0 16 16"><path fill="#fff" d="M3 2h3l1.5 3.5-2 1.3a9 9 0 0 0 3.7 3.7l1.3-2L14 10v3a1.5 1.5 0 0 1-1.6 1.5C7 14 2 9 1.5 3.6A1.5 1.5 0 0 1 3 2z"/></svg>
          <span>555 0142 3876</span>
        </li>
        <li>
          <svg viewBox="0 0 16 16"><rect x="1" y="3" width="14" height="10" rx="1" fill="#fff"/><path d="M1.5 3.5 8 9l6.5-5.5" fill="none" stroke="var(--brand-blue)" stroke-width="1.4"/></svg>
          <span>mark@tallpinecomputing.com</span>
        </li>
        <li>
          <svg viewBox="0 0 16 16"><circle cx="8" cy="8" r="6.5" fill="none" stroke="#fff" stroke-width="1.6"/><path d="M1.5 8h13M8 1.5c-3 3.5-3 9.5 0 13M8 1.5c3 3.5 3 9.5 0 13" fill="none" stroke="#fff" stroke-width="1.2"/></svg>
          <span>www.tallpinecomputing.com</span>
        </li>
      </ul>
    </div>

    <div class="brand">
      <span class="brand-dot" aria-hidden="true"></span>
      <p class="brand-name">Tall Pine<br>Computing</p>
    </div>
  </section>
</main>
</body>
</html>
```